Advanced Therapeutic Massage Therapist

I need a business card advertising my massage services as an advanced therapeutic massage therapist. I offer advanced therapeutic massage, swedish and deep tissue. I want to create a simple, professional and feminine card. I like bright colours and creativity.

I prefer a bold and experimental approach rather than something status-quo. A card to suggest therapeutic healing through dynamic massage. Motifs, shapes or layout which suggest movement and flow.
Updates

Target Market(s)

Everybody!

Industry/Entity Type

Health And Wellness

Contact Information for Business Card

The card should include:
My name, logo, services offered and my contact details.

Sláine Dunleavy
Massage Therapist

- Swedish - Deep Tissue - Advanced Therapeutic

Phone: (+353) 87 216 4093
Email: regenerate@slainedunleavy-example.com
Website: www.slainedunlevy-example.com

Font styles to use
Serif
Sans Serif
Decorative
Script

Colors

Designer to choose colors to be used in the design.

Requirements
Must have
• An example may contain something like this, yet concise:
• "Sláine Dunleavy
• Massage Therapist
• - Swedish - Deep Tissue - Advanced Therapeutic"
Nice to have
• This sentence is optional:
• Imagery such as a logo or symbol. I have attached a file containing a logo I had produced however the name is incorrect now as it is "Sláine" not "Nelly". It could be edited to change it to Sláine.
• I have sent the file as .psd .jpg. .pdf and .png
• I like when the card conveys energy, movement, pressure points, flow etc.
• I just like the designer to follow their own style and ideas. I like bright colours but must have a lot of a base colour to offset it. I really prefer them to follow their own inspiration. That is my preference.
Should not have
• Pine trees, non-native trees to Britain and Ireland, exotic flowers or animals that are not native to Britain and Ireland.
• I don't like brown as the background colour of the card.
• The cars shouldn't look like a wedding invitation i.e too many floral type designs.

```html
<!DOCTYPE html>
<html lang="en">
<head>
<meta charset="utf-8">
<title>Sláine Dunleavy – Massage Therapist Business Card</title>
<link rel="stylesheet" href="https://fonts.googleapis.com/css2?family=Great+Vibes&family=Open+Sans:wght@400;700&display=swap">
<style>
  :root {
    --page-bg: #e9e6e2;
    --card-black: #0e0e0e;
    --card-edge: #1c1c1c;
    --gold: #c8963e;
    --gold-dark: #8a5f1f;
    --mint-light: #d6efe9;
    --mint: #a9d6cc;
    --text-white: #f4f4f2;
    --text-soft: #cfcfcb;
    --divider: #3a3a3a;
    --bullet: #c9d8b6;
  }
  * { box-sizing: border-box; margin: 0; padding: 0; }
  html, body {
    width: 1200px; height: 900px; overflow: hidden;
    background: var(--page-bg);
    font-family: "Open Sans", Arial, sans-serif;
  }
  .card-sheet {
    width: 1200px; height: 900px;
    display: flex; align-items: center; justify-content: center; gap: 40px;
  }
  .card {
    position: relative;
    width: 540px; height: 310px;
    background: var(--card-black);
    border: 1px solid var(--card-edge);
    box-shadow: 0 6px 18px rgba(0,0,0,.25);
    overflow: hidden;
  }
  .logo-disc {
    position: absolute;
    border-radius: 50%;
    background: radial-gradient(circle at 45% 40%, var(--mint-light), var(--mint) 75%);
    border: 6px solid var(--gold);
    box-shadow: 0 0 0 3px var(--gold-dark);
  }
  /* contact side */
  .card--contact .logo-disc { width: 168px; height: 168px; left: 58px; top: 71px; }
  .card--contact .divider {
    position: absolute; left: 285px; top: 40px; bottom: 40px;
    width: 1px; background: var(--divider);
  }
  .contact-list {
    position: absolute; left: 305px; top: 62px;
    list-style: none; color: var(--text-soft); font-size: 13.5px; line-height: 22px;
  }
  .contact-list li { display: flex; align-items: center; gap: 8px; }
  .contact-list svg { width: 12px; height: 12px; fill: var(--gold); flex: none; }
  .service-list {
    position: absolute; left: 305px; top: 130px;
    list-style: none; color: var(--text-white);
    font-weight: 700; font-size: 16px; line-height: 24px;
  }
  .service-list li { display: flex; align-items: center; gap: 8px; }
  .service-list li::before {
    content: ""; width: 10px; height: 10px; border-radius: 50%;
    background: var(--bullet); flex: none;
  }
  /* name side */
  .card--name .logo-disc { width: 150px; height: 150px; left: 195px; top: 44px; }
  .name-block { position: absolute; left: 260px; top: 200px; text-align: right; }
  .therapist-name {
    font-family: "Great Vibes", cursive; font-weight: 400;
    font-size: 36px; color: var(--text-white); line-height: 1;
  }
  .therapist-role {
    font-size: 13px; letter-spacing: 1px; color: var(--text-soft);
    margin-top: 2px; padding-right: 6px;
  }
</style>
</head>
<body>
<main class="card-sheet">
  <section class="card card--contact">
    <div class="logo-disc" role="img" aria-label="Circular gold and mint tree emblem"></div>
    <div class="divider"></div>
    <ul class="contact-list">
      <li><svg viewBox="0 0 24 24" aria-hidden="true"><path d="M6.6 10.8a15 15 0 0 0 6.6 6.6l2.2-2.2c.3-.3.7-.4 1-.2 1.1.4 2.3.6 3.6.6.6 0 1 .4 1 1V20c0 .6-.4 1-1 1A17 17 0 0 1 3 4c0-.6.4-1 1-1h3.5c.6 0 1 .4 1 1 0 1.3.2 2.5.6 3.6.1.3 0 .7-.2 1z"/></svg>(+353) 87 216 4093</li>
      <li><svg viewBox="0 0 24 24" aria-hidden="true"><path d="M2 5h20v14H2z M3 6l9 7 9-7" stroke="#0e0e0e" stroke-width="1.5"/></svg>slainemassage@example.com</li>
    </ul>
    <ul class="service-list">
      <li>Swedish</li>
      <li>Deep Tissue</li>
      <li>Advanced Therapeutic</li>
    </ul>
  </section>
  <section class="card card--name">
    <div class="logo-disc" role="img" aria-label="Circular gold and mint tree emblem"></div>
    <div class="name-block">
      <h1 class="therapist-name">Sláine Dunleavy</h1>
      <p class="therapist-role">massage therapist</p>
    </div>
  </section>
</main>
</body>
</html>
```